Harrowmere Freight, Project

Company Profile
Harrowmere Freight Sdn Bhd is a well established and experienced freight forwarder in Kuala Lumpur, Malaysia. We specialize in air and sea forwarding, Custom Brokerage and regulatory compliance services, inland transportation,
overseas freighting and warehousing and distribution management. With our dedicated qualified and experienced professionals, we are fully committed to serving our clients.

Our Mission
Based on the motto “Quick, Reliable and Polite”, Harrowmere Freight is dedicated to upholding the following three points corporate philosophy:
1. Adhering to the principle that “the customer always comes first”.
2. Contributing to the development of the local community.
3. Making it our duty to be responsible and sincere.

Our Edge
• One-Stop Logistics Solutions
• Extensive Network Throughout Malaysia
• Highly Qualified and Experienced Pool of Professionals
• Comprehensive IT Solutions
• Innovative and Customer-focused Solutions
• Flexible and Consistent in Managing Exceptions
• Total Supply Chain Visibility

Target Market(s)

We sell the logistics services to all the industry in Malaysia. (ONE Stop Logistics Solutions)

Industry/Entity Type

Logistic

Contact Information for Business Card

I want the back of the card to be white with the logo and slogan. i would like to see the logo on the front with the general info.

Requirements
Must have
• Name, Title, Office, Cell, Fax, Email, Address, Website
Nice to have
• Modern Design Business Card

```html
<!DOCTYPE html>
<html lang="en">
<head>
<meta charset="utf-8">
<title>Harrowmere Freight – Business Card</title>
<link rel="stylesheet" href="https://fonts.googleapis.com/css2?family=Open+Sans:wght@400;600;700&display=swap">
<style>
  :root {
    --blue: #2a9ddb;
    --blue-light: #46b2e8;
    --blue-dark: #1c86c4;
    --grey: #8a8a8a;
    --grey-light: #d4d4d4;
    --ink: #3a3a3a;
    --white: #ffffff;
    --page: #eceff2;
  }
  * { box-sizing: border-box; margin: 0; padding: 0; }
  html, body { width: 1200px; height: 950px; overflow: hidden; }
  body {
    background: var(--page);
    font-family: "Open Sans", Arial, sans-serif;
    position: relative;
  }
  .card {
    position: absolute;
    width: 640px;
    height: 366px;
    border-radius: 22px;
    overflow: hidden;
    background: var(--white);
    box-shadow: 0 6px 20px rgba(0,0,0,.18);
  }

  /* ---------- Back card ---------- */
  .card--back { left: 110px; top: 80px; }
  .services {
    position: absolute; left: 34px; top: 62px;
  }
  .services__title {
    color: var(--blue-dark);
    font-weight: 700;
    font-size: 19px;
    margin-bottom: 8px;
  }
  .services__list { list-style: none; }
  .services__list li {
    font-size: 14px;
    line-height: 19.5px;
    color: var(--ink);
    padding-left: 16px;
    position: relative;
  }
  .services__list li::before {
    content: "";
    position: absolute; left: 2px; top: 7px;
    width: 6px; height: 6px; border-radius: 50%;
    background: var(--blue);
  }
  .brand-block {
    position: absolute; left: 340px; top: 110px; width: 270px;
    text-align: center;
  }
  .brand-name {
    font-weight: 700;
    font-size: 27px;
    color: var(--ink);
    letter-spacing: .2px;
  }
  .brand-dot {
    width: 46px; height: 46px; border-radius: 50%;
    background: var(--blue);
    margin: 0 auto 18px;
  }
  .slogan {
    margin-top: 16px;
    color: var(--blue-dark);
    font-weight: 600;
    font-size: 15px;
    letter-spacing: .4px;
  }

  /* ---------- Front card ---------- */
  .card--front { left: 450px; top: 500px; }
  .card__shape { position: absolute; inset: 0; }
  .contact {
    position: absolute; left: 28px; top: 26px; width: 300px;
    color: var(--white);
  }
  .contact__name { font-weight: 700; font-size: 25px; line-height: 30px; }
  .contact__title { font-size: 14px; line-height: 19px; }
  .contact__email { font-size: 13px; line-height: 18px; }
  .divider {
    border: 0; border-top: 2px dotted rgba(255,255,255,.85);
    margin: 9px 0 8px; width: 290px;
  }
  .company { font-weight: 700; font-size: 12.5px; line-height: 17px; }
  .address { font-size: 12.5px; line-height: 17px; font-style: normal; }
  .lines { list-style: none; }
  .lines li {
    font-size: 13.5px; line-height: 21px;
    display: flex; align-items: center; gap: 10px;
  }
  .lines svg { width: 14px; height: 14px; flex: none; fill: var(--white); }
  .front-brand {
    position: absolute; left: 398px; top: 150px; width: 230px;
    text-align: center;
  }
  .front-brand .brand-name { font-size: 24px; }
</style>
</head>
<body>

  <!-- Back of card -->
  <section class="card card--back" aria-label="Business card back">
    <div class="services">
      <h2 class="services__title">We're Specialize In</h2>
      <ul class="services__list">
        <li>International Shipping (Air / Sea)</li>
        <li>Consolidation – NVOCC</li>
        <li>Project Management</li>
        <li>Supply Chain Management</li>
        <li>Tax Exemption Consultancy</li>
        <li>Custom Brokerage</li>
        <li>Transportation / Haulage</li>
        <li>Warehousing</li>
        <li>Packing</li>
        <li>Marine Insurance</li>
        <li>Distribution</li>
        <li>Door to Door</li>
      </ul>
    </div>
    <div class="brand-block">
      <div class="brand-dot"></div>
      <div class="brand-name">Harrowmere Freight</div>
      <div class="slogan">ONE STOP LOGISTICS SOLUTIONS</div>
    </div>
  </section>

  <!-- Front of card -->
  <section class="card card--front" aria-label="Business card front">
    <svg class="card__shape" viewBox="0 0 640 366" preserveAspectRatio="none" aria-hidden="true">
      <defs>
        <linearGradient id="blueBand" x1="0" y1="0" x2="0" y2="1">
          <stop offset="0" stop-color="#4cb6ea"/>
          <stop offset="1" stop-color="#2496d6"/>
        </linearGradient>
        <linearGradient id="greySwoosh" x1="0" y1="0" x2="0" y2="1">
          <stop offset="0" stop-color="#e6e6e6"/>
          <stop offset="1" stop-color="#8c8c8c"/>
        </linearGradient>
      </defs>
      <path d="M0,0 H348 C372,120 392,250 440,366 H0 Z" fill="url(#greySwoosh)"/>
      <path d="M0,0 H334 C356,120 374,250 418,366 H0 Z" fill="url(#blueBand)"/>
    </svg>

    <div class="contact">
      <h1 class="contact__name">Faizal Rahman</h1>
      <p class="contact__title">Managing Director</p>
      <p class="contact__email">faizal.rahman@harrowmere.com.my</p>
      <hr class="divider">
      <p class="company">HARROWMERE FREIGHT SDN. BHD. (1246830-K)</p>
      <address class="address">No. 8B, 2nd Floor, Jalan Seri Kenari 3,<br>Taman Kenari Indah, 41050 Klang,<br>Selangor Darul Ehsan, Malaysia.</address>
      <hr class="divider">
      <ul class="lines">
        <li>
          <svg viewBox="0 0 16 16" aria-label="Office"><path d="M3.6 1.2l2.3 2.6-1.3 1.6c.9 2 2.4 3.5 4.4 4.4l1.6-1.3 2.6 2.3-1.4 2.6C6.6 13.2 2.8 9.4 1 4z"/></svg>
          (603) 5521 7140 / 7150
        </li>
        <li>
          <svg viewBox="0 0 16 16" aria-label="Mobile"><path d="M4.5 1h7a1 1 0 0 1 1 1v12a1 1 0 0 1-1 1h-7a1 1 0 0 1-1-1V2a1 1 0 0 1 1-1zm1 2v9h5V3z"/></svg>
          +6012-418 2093
        </li>
        <li>
          <svg viewBox="0 0 16 16" aria-label="Fax"><path d="M4 1h8v4H4zM2 6h12a1 1 0 0 1 1 1v6H1V7a1 1 0 0 1 1-1zm2 4v4h8v-4z"/></svg>
          (603) 5521 7160
        </li>
        <li>
          <svg viewBox="0 0 16 16" aria-label="Website"><path d="M8 1a7 7 0 1 0 0 14A7 7 0 0 0 8 1zm0 2a5 5 0 0 1 4.9 4H10.5c-.1-1.6-.5-3-1.2-3.9A5 5 0 0 1 8 3zM6 9h4c-.2 2-1 3.5-2 3.5S6.2 11 6 9zm0-2c.2-2 1-3.5 2-3.5s1.8 1.5 2 3.5z"/></svg>
          harrowmere.com.my
        </li>
      </ul>
    </div>

    <div class="front-brand">
      <div class="brand-dot"></div>
      <div class="brand-name">Harrowmere Freight</div>
    </div>
  </section>

</body>
</html>
```